Musician looking for catchy Web Design for promotion

My name is Brenna Coyle. I'm an Irish musician who plays the tin whistle and the flute. I'm also the leader of a traditional Irish music and dance ensemble called Gather the Willows (www.gatherthewillows-example.com) and for the past 30 years, I've toured the world performing thousands of concerts. I run an annual cruise (www.brennacoylevoyage-example.com) that I would like a link to, and I'm also I'm organizing tours to Ireland that I would like a page set up for. I'm looking for a website to promote my tours and my music.
Updates

Hello Graphic Designers, I am only looking for the design of the home page to make my decision. Thank you. Brenna

Target Market(s)

Music fans of Irlsh and World Music

Industry/Entity Type

Entertainment Industry

Number of Pages Required

5+ page

Requirements
Must have
• I'm looking for a catchy design that shows a photo of me. I would like a few links....
• BIO
• TOURDATES
• BRENNA COYLE CRUISE
• MUSICAL TOUR OF IRELAND
• CONTACT
• VIDEO
• GALLERY
• CONTACT
• MAILING LIST
• STORE
Nice to have
• we'll see!

```html
<!DOCTYPE html>
<html lang="en">
<head>
<meta charset="utf-8">
<title>Brenna Coyle — Irish Musician</title>
<link rel="stylesheet" href="https://fonts.googleapis.com/css2?family=Lustria&family=Lato:wght@400;700&display=swap">
<style>
:root{
  --orange:#f5a21a;
  --orange-dark:#d98a0b;
  --ink:#ffffff;
  --muted:#c9c9c9;
  --bg-dark:#2a2a2a;
  --bg-darker:#1c1c1c;
  --bg-black:#080808;
  --row-light:#5b5b5b;
  --row-dark:#3c3c3c;
  --frame:#ffffff;
}
*{box-sizing:border-box;margin:0;padding:0}
html,body{width:1200px;height:4423px;overflow:hidden;background:var(--bg-dark)}
body{font-family:"Lato",Arial,sans-serif;color:var(--ink);position:relative}
.serif{font-family:"Lustria",Georgia,serif}
section,header,footer,nav{position:absolute;left:0;width:1200px}
.abs{position:absolute}
.accent{color:var(--orange)}
.heading{font-family:"Lustria",Georgia,serif;font-size:44px;font-weight:400;color:var(--ink)}
.heading.center{position:absolute;left:0;width:1200px;text-align:center}
.btn{position:absolute;background:var(--orange);color:#fff;font-family:"Lato",sans-serif;font-weight:700;font-size:15px;text-align:center;border-radius:2px}
.placeholder{position:absolute}

/* header */
.site-header{top:0;height:148px;background:var(--bg-darker)}
.contact-icon{position:absolute;width:32px;height:32px;border-radius:50%;background:var(--orange)}
.contact-label{position:absolute;font-size:15px;color:var(--orange)}
.contact-value{position:absolute;font-size:14px;color:var(--ink)}
.brand{position:absolute;left:400px;top:26px;width:400px;text-align:center;font-family:"Lustria",Georgia,serif;color:var(--ink)}
.brand .name{font-size:28px;letter-spacing:1px;line-height:34px}
.brand .tag{font-size:28px;letter-spacing:1px;line-height:34px}
.brand-dot{position:absolute;left:385px;top:50px;width:14px;height:14px;border-radius:50%;background:var(--orange)}
.main-nav{top:148px;height:38px;background:#111;border-top:1px solid #333}
.main-nav ul{list-style:none;display:flex;justify-content:space-between;padding:0 100px 0 105px;line-height:38px;font-size:15px}
.main-nav li.active{color:var(--orange);border-bottom:3px solid var(--orange);line-height:33px}

/* hero */
.hero{top:186px;height:556px;background:var(--bg-dark)}
.hero-frame{position:absolute;left:72px;top:6px;width:1056px;height:546px;border:6px solid var(--frame);background:linear-gradient(135deg,#5b4a34,#3a3327 45%,#6d5a40 75%,#2e2a22)}
.hero-caption{position:absolute;left:120px;top:345px;width:810px;height:124px;background:rgba(0,0,0,.55);text-align:center}
.hero-caption h1{font-family:"Lustria",Georgia,serif;font-weight:400;font-size:38px;margin-top:18px}
.hero-caption p{font-size:20px;margin-top:8px}

/* about */
.about{top:742px;height:503px;background:var(--bg-dark)}
.about .heading{position:absolute;left:82px;top:36px;font-size:40px}
.facts{position:absolute;left:82px;top:116px;font-size:14px;line-height:22px}
.facts .row{display:flex}
.facts .k{width:120px;color:var(--orange)}
.facts .v{width:560px}
.bio{position:absolute;left:82px;top:278px;width:680px;font-size:13px;line-height:22px;color:var(--muted)}
.bio b{color:var(--ink)}
.socials{position:absolute;left:82px;top:380px;display:flex;gap:10px}
.socials span{width:34px;height:34px;border-radius:50%;border:2px solid var(--orange);background:#3a3a3a}
.read-more{position:absolute;left:570px;top:398px;font-size:15px;color:var(--orange)}
.instrument{position:absolute;width:118px;height:118px;border-radius:50%;border:5px solid var(--orange);background:radial-gradient(circle,#6a5a45,#2a241d);display:flex;align-items:center;justify-content:center;text-align:center;font-weight:700;font-size:16px;line-height:18px}

/* tours */
.tours{top:1245px;height:677px;background:var(--bg-black)}
.tour{position:absolute;left:78px;width:1042px;height:108px}
.tour .date{position:absolute;left:0;top:0;width:158px;height:108px;text-align:center}
.tour .date.hot{background:var(--orange)}
.tour .date.cool{background:#d8d8d8;color:#222}
.tour .day{font-family:"Lustria",Georgia,serif;font-size:48px;line-height:56px;margin-top:10px}
.tour .mon{font-size:16px}
.tour .title{position:absolute;left:158px;top:0;width:884px;height:54px;background:var(--row-light);font-family:"Lustria",Georgia,serif;font-size:24px;line-height:54px;padding-left:24px}
.tour .info{position:absolute;left:158px;top:54px;width:884px;height:54px;background:var(--row-dark);font-size:14px;line-height:54px;padding-left:24px}
.tour .info span{margin-right:100px}
.tour .info svg{vertical-align:-4px;margin-right:8px}
.tour .btn{left:920px;top:16px;width:112px;height:30px;line-height:30px;font-size:14px}
.tour .avail{position:absolute;left:920px;top:60px;width:112px;text-align:center;font-size:12px;color:var(--muted)}

/* store */
.store{top:1922px;height:548px;background:linear-gradient(#2f2f2f,#252525)}
.album{position:absolute;top:134px;width:256px;text-align:center}
.album .cover{height:246px;border:7px solid var(--frame)}
.album .t{margin-top:26px;font-size:16px}
.album .p{margin-top:10px;font-size:16px;color:var(--muted)}
.album .btn{position:relative;display:inline-block;width:84px;height:28px;line-height:28px;margin-top:14px;font-size:14px}
.arrow{position:absolute;font-size:44px;color:#ddd;font-family:"Lato",sans-serif}

/* gallery */
.gallery{top:2470px;height:596px;background:var(--bg-darker)}
.photo{position:absolute}

/* videos & critics */
.media{top:3066px;height:589px;background:var(--bg-dark)}
.media .heading{position:absolute;font-size:40px}
.video-main{position:absolute;left:80px;top:120px;width:490px;height:242px;background:linear-gradient(135deg,#4a4236,#2a2620 60%,#5a4c3a)}
.thumb{position:absolute;top:372px;width:88px;height:86px;background:linear-gradient(135deg,#6a6a6a,#2e2e2e);border:2px solid #111}
.quote{position:absolute;left:630px;width:490px;font-size:13px;line-height:21px;font-style:italic;color:var(--muted)}
.quote .by{font-style:normal;text-align:right;margin-top:8px;color:var(--ink)}
.quote .by b{color:var(--orange)}
.rule{position:absolute;left:630px;width:490px;height:1px;background:#555}

/* artists */
.artists{top:3655px;height:502px;background:var(--bg-black)}
.artist{position:absolute;top:128px;width:210px;text-align:center}
.artist .pic{width:190px;height:190px;margin:0 auto;border-radius:50%;border:6px solid var(--frame);background:radial-gradient(circle at 50% 40%,#7a6650,#3b3128);position:relative}
.artist .badge{position:absolute;right:6px;bottom:10px;width:34px;height:34px;border-radius:50%;background:var(--orange);border:3px solid #fff}
.artist .n{margin-top:14px;color:var(--orange);font-size:15px;font-weight:700}
.artist .r{font-size:14px;color:var(--muted);margin-top:4px}
.artist .d{font-size:13px;line-height:19px;margin-top:8px;padding:0 14px}

/* footer */
.site-footer{top:4157px;height:266px;background:#2c2c2c}
.foot-brand{position:absolute;left:400px;top:28px;width:400px;text-align:center;font-family:"Lustria",Georgia,serif;font-size:22px;line-height:28px;color:#ddd}
.foot-col{position:absolute;top:140px;display:flex;gap:16px;font-size:14px;line-height:22px}
.foot-col .lbl{color:var(--orange);font-weight:700}
.foot-bar{position:absolute;left:0;top:238px;width:1200px;height:28px;background:#1a1a1a;font-size:13px;line-height:28px}
</style>
</head>
<body>

<header class="site-header">
  <span class="contact-icon" style="left:82px;top:20px"></span>
  <svg class="abs" style="left:89px;top:30px" width="18" height="13" viewBox="0 0 18 13"><rect x="1" y="1" width="16" height="11" fill="none" stroke="#fff" stroke-width="1.6"/><path d="M1 1l8 6 8-6" fill="none" stroke="#fff" stroke-width="1.6"/></svg>
  <span class="contact-label" style="left:124px;top:18px">Mail Me:</span>
  <span class="contact-value" style="left:124px;top:38px">info@brennacoylevoyage-example.com</span>
  <span class="contact-icon" style="left:82px;top:96px;width:26px;height:26px"></span>
  <span class="contact-value" style="left:120px;top:100px">Cart (0)</span>

  <span class="brand-dot"></span>
  <div class="brand"><div class="name">BRENNA COYLE'S</div><div class="tag">MUSICAL TOUR OF IRELAND</div></div>

  <span class="contact-icon" style="left:985px;top:20px"></span>
  <svg class="abs" style="left:993px;top:28px" width="16" height="16" viewBox="0 0 16 16"><path d="M3 1l3 3-2 2c1 2 3 4 5 5l2-2 3 3-2 3C7 15 1 9 0 3z" fill="#fff"/></svg>
  <span class="contact-label" style="left:1026px;top:18px">Call Me:</span>
  <span class="contact-value" style="left:1026px;top:38px">855-555-0142</span>
  <div class="btn" style="left:970px;top:96px;width:150px;height:32px;line-height:32px">Book My Tour</div>
</header>

<nav class="main-nav">
  <ul>
    <li class="active">Home</li><li>Bio</li><li>Tour Dates</li><li>Brenna Coyle Cruise</li><li>Musical Tour Of Ireland</li><li>Videos</li><li>Gallery</li><li>Store</li><li>Contact Us</li>
  </ul>
</nav>

<section class="hero">
  <div class="hero-frame" role="img" aria-label="Portrait of Brenna Coyle standing between ornate iron gates">
    <div class="hero-caption">
      <h1>I Am Brenna Coyle</h1>
      <p>I Am An Irish Musician Who Plays The Tin Whistle &amp; The Flute</p>
    </div>
  </div>
</section>

<section class="about">
  <h2 class="heading">About <span class="accent">Brenna Coyle</span></h2>
  <div class="facts">
    <div class="row"><span class="k">Born:</span><span class="v">1965, The Bronx, New York City, New York, United States</span></div>
    <div class="row" style="margin-top:8px"><span class="k">Movies:</span><span class="v">Purely Green Isle</span></div>
    <div class="row" style="margin-top:8px"><span class="k">Album:</span><span class="v">Tunes of the Tin Whistle, Tunes of the Tin Whistle 2, Whistle Upon the Breeze,<br>A Connemara Evening, Round the Road</span></div>
    <div class="row" style="margin-top:8px"><span class="k">Music Group:</span><span class="v accent" style="text-decoration:underline">Gather the Willows</span></div>
  </div>
  <p class="bio"><b>BRENNA COYLE</b> is considered one of the finest musicians &amp; personalities in the history of Irish music in America. She was born in the Bronx, New York, to Irish parents, and is the second oldest of seven children raised in a musical household. Her mother Margaret hails from a small village in County Clare and her father Tomas, an All-Ireland Champion accordion player, was a native of County Galway.</p>
  <div class="socials"><span></span><span></span><span></span></div>
  <span class="read-more">Read More &gt;&gt;</span>
  <div class="placeholder" role="img" aria-label="Photo of Brenna Coyle playing the tin whistle" style="left:900px;top:28px;width:230px;height:475px;background:linear-gradient(180deg,#2a2a2a,#4a3a2c 40%,#5a4636 70%,#2a2a2a)"></div>
  <div class="instrument" role="img" aria-label="Flute" style="left:788px;top:120px">Flute</div>
  <div class="instrument" role="img" aria-label="Tin whistle" style="left:768px;top:262px">Tin<br>Whistle</div>
</section>

<section class="tours">
  <h2 class="heading center" style="top:50px">Upcoming <span class="accent">Tours</span></h2>
  <div class="tour" style="top:140px">
    <div class="date hot"><div class="day">10</div><div class="mon">Feb, 2016</div></div>
    <div class="title">Ireland Tour Lorem Ipsum</div>
    <div class="info"><span><svg width="14" height="14" viewBox="0 0 14 14"><circle cx="7" cy="7" r="6" fill="none" stroke="#f5a21a" stroke-width="1.6"/><path d="M7 3v4l3 2" stroke="#f5a21a" stroke-width="1.6" fill="none"/></svg>9:00 AM</span><span><svg width="12" height="16" viewBox="0 0 12 16"><path d="M6 15S1 9 1 6a5 5 0 0110 0c0 3-5 9-5 9z" fill="none" stroke="#f5a21a" stroke-width="1.6"/><circle cx="6" cy="6" r="2" fill="#f5a21a"/></svg>Lorem Ipsum, Dolor Sit, City Code - 1234</span></div>
    <div class="btn">Get Tickets</div><div class="avail">Now Available Here</div>
  </div>
  <div class="tour" style="top:252px">
    <div class="date cool"><div class="day">03</div><div class="mon">Feb, 2016</div></div>
    <div class="title">Lorem Ipsum Tour</div>
    <div class="info"><span><svg width="14" height="14" viewBox="0 0 14 14"><circle cx="7" cy="7" r="6" fill="none" stroke="#f5a21a" stroke-width="1.6"/><path d="M7 3v4l3 2" stroke="#f5a21a" stroke-width="1.6" fill="none"/></svg>9:00 AM</span><span><svg width="12" height="16" viewBox="0 0 12 16"><path d="M6 15S1 9 1 6a5 5 0 0110 0c0 3-5 9-5 9z" fill="none" stroke="#f5a21a" stroke-width="1.6"/><circle cx="6" cy="6" r="2" fill="#f5a21a"/></svg>Lorem Ipsum, Dolor Sit, City Code - 1234</span></div>
    <div class="btn">Get Tickets</div><div class="avail">Now Available Here</div>
  </div>
  <div class="tour" style="top:364px">
    <div class="date hot"><div class="day">13</div><div class="mon">Feb, 2016</div></div>
    <div class="title">Ireland Tour Lorem Ipsum</div>
    <div class="info"><span><svg width="14" height="14" viewBox="0 0 14 14"><circle cx="7" cy="7" r="6" fill="none" stroke="#f5a21a" stroke-width="1.6"/><path d="M7 3v4l3 2" stroke="#f5a21a" stroke-width="1.6" fill="none"/></svg>9:00 AM</span><span><svg width="12" height="16" viewBox="0 0 12 16"><path d="M6 15S1 9 1 6a5 5 0 0110 0c0 3-5 9-5 9z" fill="none" stroke="#f5a21a" stroke-width="1.6"/><circle cx="6" cy="6" r="2" fill="#f5a21a"/></svg>Lorem Ipsum, Dolor Sit, City Code - 1234</span></div>
    <div class="btn">Get Tickets</div><div class="avail">Now Available Here</div>
  </div>
  <div class="tour" style="top:476px">
    <div class="date cool"><div class="day">03</div><div class="mon">Feb, 2016</div></div>
    <div class="title">Ireland Tour Lorem Ipsum</div>
    <div class="info"><span><svg width="14" height="14" viewBox="0 0 14 14"><circle cx="7" cy="7" r="6" fill="none" stroke="#f5a21a" stroke-width="1.6"/><path d="M7 3v4l3 2" stroke="#f5a21a" stroke-width="1.6" fill="none"/></svg>9:00 AM</span><span><svg width="12" height="16" viewBox="0 0 12 16"><path d="M6 15S1 9 1 6a5 5 0 0110 0c0 3-5 9-5 9z" fill="none" stroke="#f5a21a" stroke-width="1.6"/><circle cx="6" cy="6" r="2" fill="#f5a21a"/></svg>Lorem Ipsum, Dolor Sit, City Code - 1234</span></div>
    <div class="btn">Get Tickets</div><div class="avail">Now Available Here</div>
  </div>
</section>

<section class="store">
  <h2 class="heading center" style="top:50px">My <span class="accent">Music Store</span></h2>
  <span class="arrow" style="left:28px;top:282px">&#8249;</span>
  <span class="arrow" style="left:1152px;top:282px">&#8250;</span>
  <div class="album" style="left:78px"><div class="cover" role="img" aria-label="Album cover: Tunes of the Tin Whistle" style="background:linear-gradient(180deg,#6b8fb8,#2f5a86 60%,#3d6b4a)"></div><div class="t">Tunes of the Tin Whistle</div><div class="p">$23.00</div><div class="btn">Buy Now</div></div>
  <div class="album" style="left:346px"><div class="cover" role="img" aria-label="Album cover: A Connemara Evening" style="background:linear-gradient(180deg,#9aa3ad,#5d6670 60%,#3a4048)"></div><div class="t">A Connemara Evening</div><div class="p">$23.00</div><div class="btn">Buy Now</div></div>
  <div class="album" style="left:614px"><div class="cover" role="img" aria-label="Album cover: Winter by the Hearth" style="background:linear-gradient(180deg,#b3201c,#7a1210 60%,#3f2a1c)"></div><div class="t">Winter by the Hearth</div><div class="p">$23.00</div><div class="btn">Buy Now</div></div>
  <div class="album" style="left:866px"><div class="cover" role="img" aria-label="Album cover: A Whistle Upon the Breeze" style="background:linear-gradient(135deg,#d7b04a,#3b6f8a 50%,#1f3f5a)"></div><div class="t">A Whistle Upon the Breeze</div><div class="p">$23.00</div><div class="btn">Buy Now</div></div>
</section>

<section class="gallery">
  <h2 class="heading center" style="top:50px">My <span class="accent">Gallery</span></h2>
  <div class="photo" role="img" aria-label="Brenna Coyle holding a flute" style="left:80px;top:127px;width:290px;height:365px;background:linear-gradient(135deg,#2c4f8a,#16305c 60%,#0c1a33)"></div>
  <div class="photo" role="img" aria-label="Ensemble posing on a stage" style="left:376px;top:127px;width:290px;height:160px;background:linear-gradient(135deg,#4a3b2f,#241d18)"></div>
  <div class="photo" role="img" aria-label="Musicians playing together in a pub" style="left:672px;top:127px;width:448px;height:160px;background:linear-gradient(135deg,#7a4a2a,#3a2414 60%,#5a3a20)"></div>
  <div class="photo" role="img" aria-label="Ensemble in a green-lit hall" style="left:376px;top:293px;width:290px;height:199px;background:linear-gradient(135deg,#3e6a2c,#1e3a16)"></div>
  <div class="photo" role="img" aria-label="Brenna Coyle playing the flute on stage" style="left:672px;top:293px;width:200px;height:199px;background:linear-gradient(135deg,#d88a1a,#6a3a08)"></div>
  <div class="photo" role="img" aria-label="Band performing with dancers" style="left:878px;top:293px;width:242px;height:199px;background:linear-gradient(135deg,#3a3a3a,#151515 60%,#4a3a2a)"></div>
  <div class="btn" style="left:540px;top:530px;width:120px;height:34px;line-height:34px">View Gallery</div>
</section>

<section class="media">
  <h2 class="heading" style="left:80px;top:48px">My <span class="accent">Videos</span></h2>
  <h2 class="heading" style="left:630px;top:48px">What <span class="accent">Critics Are Saying</span></h2>
  <div class="video-main" role="img" aria-label="Video still of the ensemble performing">
    <svg class="abs" style="left:215px;top:91px" width="60" height="60" viewBox="0 0 60 60"><circle cx="30" cy="30" r="28" fill="#f5a21a"/><path d="M24 18l18 12-18 12z" fill="#fff"/></svg>
  </div>
  <div class="thumb" style="left:80px" role="img" aria-label="Video thumbnail"></div>
  <div class="thumb" style="left:180px" role="img" aria-label="Video thumbnail"></div>
  <div class="thumb" style="left:280px" role="img" aria-label="Video thumbnail"></div>
  <div class="thumb" style="left:380px" role="img" aria-label="Video thumbnail"></div>
  <div class="thumb" style="left:480px" role="img" aria-label="Video thumbnail"></div>
  <div class="btn" style="left:255px;top:495px;width:140px;height:34px;line-height:34px">View All Videos</div>

  <div class="quote" style="top:124px">"When gifted tin whistle or flute players over the past quarter of a century come to mind, Irish traditional music devotees invariably will add Brenna Coyle's name to the list. Her music is pure art, compelling &amp; creative, vibrant &amp; virtuosic. It is filled with style, substance, sensitivity &amp; soul."<div class="by"><b>-Conor Whelan</b>, The Harbour Herald</div></div>
  <div class="rule" style="top:270px"></div>
  <div class="quote" style="top:288px">"Coyle has become a leading Irish flute &amp; whistle virtuoso, constantly in demand for session &amp; commercial work. She has gone on to become both a dazzling technician &amp; spellbinding interpreter of slow airs. She displays a range of texture &amp; emotion that many singers would envy."<div class="by"><b>-Maeve Dorsey</b>, The Eastern Gazette</div></div>
  <div class="btn" style="left:782px;top:495px;width:186px;height:34px;line-height:34px">View All Testimonials</div>
</section>

<section class="artists">
  <h2 class="heading center" style="top:48px">Our <span class="accent">Rocking Artists</span></h2>
  <span class="arrow" style="left:28px;top:176px">&#8249;</span>
  <span class="arrow" style="left:1152px;top:176px">&#8250;</span>
  <div class="artist" style="left:40px"><div class="pic" role="img" aria-label="Portrait of Brenna Coyle"><span class="badge"></span></div><div class="n">BRENNA COYLE</div><div class="r">Flute, Tin Whistle</div><div class="d">is internationally recognized as one of the greatest...</div></div>
  <div class="artist" style="left:278px"><div class="pic" role="img" aria-label="Portrait of Nora Keane"><span class="badge"></span></div><div class="n">NORA KEANE</div><div class="r">Drum</div><div class="d">was born in New York &amp; raised in a musical household...</div></div>
  <div class="artist" style="left:496px"><div class="pic" role="img" aria-label="Portrait of Aisling Treacy"><span class="badge"></span></div><div class="n">AISLING TREACY</div><div class="r">Accordion</div><div class="d">grew up in a seaside town, near the west coast...</div></div>
  <div class="artist" style="left:706px"><div class="pic" role="img" aria-label="Portrait of Siobhan Rourke"><span class="badge"></span></div><div class="n">SIOBHAN ROURKE</div><div class="r">Base Guitar</div><div class="d">from the north coast, &amp; comes from a family...</div></div>
  <div class="artist" style="left:921px"><div class="pic" role="img" aria-label="Portrait of Declan Furey"><span class="badge"></span></div><div class="n">DECLAN FUREY</div><div class="r">Dance</div><div class="d">is our set dance &amp; ceili dance caller &amp; instructor...</div></div>
</section>

<footer class="site-footer">
  <div class="foot-brand">BRENNA COYLE'S<br>MUSICAL TOUR OF IRELAND</div>
  <div class="foot-col" style="left:90px">
    <svg width="34" height="34" viewBox="0 0 34 34"><circle cx="17" cy="17" r="15" fill="none" stroke="#ddd" stroke-width="2"/><path d="M11 13h12v9H11z M11 13l6 5 6-5" fill="none" stroke="#ddd" stroke-width="1.6"/></svg>
    <div><div class="lbl">BOOKING INQUIRIES:</div><div>book@brennacoylevoyage-example.com</div></div>
  </div>
  <div class="foot-col" style="left:470px">
    <svg width="34" height="34" viewBox="0 0 34 34"><circle cx="17" cy="17" r="15" fill="none" stroke="#ddd" stroke-width="2"/><path d="M12 10l3 3-2 2c1 2 3 4 5 5l2-2 3 3-2 3c-5-1-10-6-11-11z" fill="#ddd"/></svg>
    <div><div class="lbl">PHONE:</div><div>1-855-555-0199 (855-555-0142)</div></div>
  </div>
  <div class="foot-col" style="left:850px">
    <svg width="34" height="34" viewBox="0 0 34 34"><circle cx="17" cy="17" r="15" fill="none" stroke="#ddd" stroke-width="2"/><path d="M11 13h12v9H11z M11 13l6 5 6-5" fill="none" stroke="#ddd" stroke-width="1.6"/></svg>
    <div><div class="lbl">GENERAL INFORMATION:</div><div>info@brennacoylevoyage-example.com</div></div>
  </div>
  <div class="foot-bar">
    <span class="abs accent" style="left:82px">Gather the Willows &nbsp;|&nbsp; Annual Cruise</span>
    <span class="abs" style="right:82px">Copyright 2016 Brenna Coyle Music. All Rights Reserved.</span>
  </div>
</footer>

</body>
</html>
```